Modern Business Card for Larkwell 2018

Our company assumes the best about people. We are creating an online community of entrepreneurs and business leaders who struggle with marketing their business online.

This business card should POP! We recently got a new logo and are launching a new website next month, so our business cards should make a statement that feels:
-Fresh
-Smart
-Trustworthy
-Fun

Target Market(s)

small business owners, entrepreneurs

Industry/Entity Type

Digital Marketing

Contact Information for Business Card

Dimensions: 3.5" x 2"

Font styles to use
Sans Serif

Colors
f37122
ffffff

Requirements
Must have
• We need a business card with a modern, bold design. We will use one side of the card as a lead-generation offer, so text on one side will need to fit up to 140 characters. The business card should stick to our core colors (orange, black, and white).
Nice to have
• We think a vertical "portrait" design could be interesting.
Should not have
• Should not look like a traditional business card. The round icon should stand out from a distance.

```html
<!DOCTYPE html>
<html lang="en">
<head>
<meta charset="utf-8">
<title>Larkwell Business Card</title>
<link rel="stylesheet" href="https://fonts.googleapis.com/css2?family=Montserrat:wght@600;700&family=Roboto+Condensed:wght@400;700&family=Roboto:wght@400;500&display=swap">
<style>
  :root {
    --orange: #e05a23;
    --white: #ffffff;
    --paper: #f2f2f2;
    --ink: #1e1e1e;
    --backdrop: #3b3b3b;
  }
  * { margin: 0; padding: 0; box-sizing: border-box; }
  html, body { width: 1200px; height: 751px; overflow: hidden; }
  body { background: var(--backdrop); position: relative; font-family: "Roboto", sans-serif; }

  .card {
    position: absolute; top: 219px; width: 493px; height: 281px;
    background: var(--orange); overflow: hidden;
  }
  .card--front { left: 91px; }
  .card--back { left: 620px; }

  .band {
    position: absolute; left: 0; top: 178px; width: 100%; height: 84px;
    background: var(--paper);
  }

  .wordmark {
    position: absolute; font-family: "Montserrat", sans-serif; font-weight: 700;
    color: var(--white); letter-spacing: 1px; line-height: 1; white-space: nowrap;
  }
  .tagline {
    position: absolute; font-family: "Montserrat", sans-serif; font-weight: 600;
    color: var(--white); text-transform: uppercase; line-height: 1; white-space: nowrap;
  }

  /* front */
  .card--front .wordmark { left: 0; width: 100%; text-align: center; top: 61px; font-size: 34px; }
  .card--front .tagline { left: 0; width: 100%; text-align: center; top: 100px; font-size: 10px; letter-spacing: 0.8px; }
  .emblem-circle { position: absolute; left: -3px; top: 171px; }
  .contact { position: absolute; left: 0; width: 492px; padding-left: 0; top: 188px; text-align: center; }
  .contact__name { font-family: "Roboto Condensed", sans-serif; font-weight: 700; font-size: 19px; color: var(--orange); line-height: 22px; text-transform: uppercase; }
  .contact__role { font-family: "Roboto Condensed", sans-serif; font-size: 13.5px; color: var(--ink); line-height: 17px; text-transform: uppercase; }
  .contact__email { font-size: 12.5px; color: var(--ink); line-height: 17px; }

  /* back */
  .brand-dot { position: absolute; left: 115px; top: 46px; }
  .card--back .wordmark { left: 33px; width: 196px; text-align: center; top: 91px; font-size: 27px; }
  .card--back .tagline { left: 33px; width: 196px; text-align: center; top: 124px; font-size: 8.5px; letter-spacing: 0.5px; }
  .divider { position: absolute; left: 244px; top: 24px; width: 1px; height: 130px; background: rgba(255,255,255,0.55); }
  .offer { position: absolute; left: 265px; top: 23px; color: var(--white); }
  .offer__headline { font-family: "Roboto Condensed", sans-serif; font-weight: 700; font-size: 17.5px; line-height: 17px; text-transform: uppercase; }
  .offer__body { font-size: 13px; line-height: 16px; margin-top: 5px; }
  .offer__url { font-weight: 500; font-size: 16px; line-height: 20px; margin-top: 5px; }
  .write-line { position: absolute; left: 42px; width: 409px; height: 1px; background: #555; }
  .write-line--1 { top: 204px; }
  .write-line--2 { top: 237px; }
</style>
</head>
<body>
  <section class="card card--front">
    <div class="wordmark">LARKWELL</div>
    <div class="tagline">Tell stories that inspire action</div>
    <div class="band"></div>
    <svg class="emblem-circle" width="94" height="94" viewBox="0 0 94 94" aria-hidden="true">
      <circle cx="47" cy="47" r="42" fill="var(--white)" stroke="var(--orange)" stroke-width="6"/>
    </svg>
    <div class="contact">
      <p class="contact__name">Dana Whitfield</p>
      <p class="contact__role">Story Marketing Coach</p>
      <p class="contact__email">dana@larkwellnow.com</p>
    </div>
  </section>

  <section class="card card--back">
    <svg class="brand-dot" width="32" height="32" viewBox="0 0 32 32" aria-hidden="true">
      <circle cx="16" cy="16" r="15" fill="var(--white)"/>
    </svg>
    <div class="wordmark">LARKWELL</div>
    <div class="tagline">Tell stories that inspire action</div>
    <div class="divider"></div>
    <div class="offer">
      <p class="offer__headline">Reach more people.<br>Make more money.<br>Create more impact.</p>
      <p class="offer__body">Get your free Larkwell<br>Starter Package and our<br>marketing guide today at</p>
      <p class="offer__url">Larkwellnow.com/start</p>
    </div>
    <div class="band"></div>
    <div class="write-line write-line--1"></div>
    <div class="write-line write-line--2"></div>
  </section>
</body>
</html>
```